Brookvale Estates LLC stationary for a real estate property management company.

Create stationary (letterhead, envelopes, business cards) using Brookvale Estates LLC logo as primary creative element. Stationary design needs to be horizontal, leaving as much space as possible for correspondence copy. See attached Creative Brief and past stationary files for details.

Target Market(s)

Prospective apartment residents and current residents, vendors, and government agencies.

Industry/Entity Type

Property Management

Contact Information for Business Card

Business card employee title: Property Manager. Should include address, phone, fax, email, website, slogan, and Brookvale Estates logo.

Font styles to use
Sans Serif

Colors
0592cd
000000

Requirements
Must have
• Tone should be conservative, institutional, business (i.e. banking, finance, real estate). Must include: address, phone, fax, website, and slogan (see attached Creative Brief). Should be a horizontal design, leaving as much room as possible for letter correspondence copy.
Nice to have
• Please use an Arial or Helvetica style font.
Should not have
• Letterhead layout should leave as much room as possible for copy.

```html
<!DOCTYPE html>
<html lang="en">
<head>
<meta charset="utf-8">
<title>Brookvale Estates LLC – Business Card</title>
<link href="https://fonts.googleapis.com/css2?family=Roboto:wght@400;500;700&display=swap" rel="stylesheet">
<style>
  :root {
    --brand-blue: #0592cd;
    --brand-blue-deep: #0a6aa8;
    --brand-blue-light: #1bb8ec;
    --ink: #000000;
    --text-gray: #4a4a4a;
    --rule-gray: #8a8a8a;
    --band-dark: #4b4b4d;
    --card-white: #f7f7f7;
    --canvas-bg: #e6e6e6;
  }
  * { margin: 0; padding: 0; box-sizing: border-box; }
  html, body {
    width: 1200px; height: 960px; overflow: hidden;
    background: var(--canvas-bg);
    font-family: "Roboto", Arial, sans-serif;
  }
  .canvas { position: relative; width: 1200px; height: 960px; }

  .card { position: absolute; box-shadow: 0 3px 8px rgba(0,0,0,.25); overflow: hidden; }

  /* Front */
  .card-front { left: 302px; top: 130px; width: 600px; height: 342px; background: var(--card-white); }
  .brand-name { position: absolute; right: 30px; top: 62px; text-align: right; color: var(--brand-blue); font-weight: 700; line-height: 1; }
  .brand-name .line-main { display: block; font-size: 34px; letter-spacing: .5px; }
  .brand-name .line-sub { display: block; font-size: 15px; letter-spacing: 2.6px; margin-top: 5px; }

  .name-accent { position: absolute; left: 0; top: 197px; width: 9px; height: 37px; background: var(--brand-blue); }
  .person-name { position: absolute; left: 27px; top: 196px; font-size: 22px; font-weight: 500; color: var(--brand-blue); letter-spacing: .2px; }
  .person-title { position: absolute; left: 27px; top: 220px; font-size: 15px; color: var(--text-gray); }
  .title-rule { position: absolute; left: 160px; right: 30px; top: 230px; height: 1px; background: var(--rule-gray); }

  .contact-list { position: absolute; left: 27px; top: 248px; list-style: none; font-size: 14px; color: var(--text-gray); }
  .contact-list li { display: flex; align-items: center; height: 19.5px; }
  .contact-list svg { width: 14px; height: 12px; margin-right: 9px; fill: var(--brand-blue-deep); }

  .address-block { position: absolute; right: 29px; top: 248px; text-align: right; font-size: 14px; color: var(--text-gray); line-height: 19px; }

  .band-blue { position: absolute; left: 0; top: 325px; width: 310px; height: 10px; background: var(--brand-blue-deep); }
  .band-mark { position: absolute; left: 305px; top: 309px; width: 26px; height: 33px; background: var(--brand-blue-deep); }
  .slogan-band { position: absolute; left: 334px; top: 316px; right: 0; height: 26px; background: var(--band-dark); color: #fff; font-size: 14px; display: flex; align-items: center; padding-left: 20px; }

  /* Back */
  .card-back { left: 299px; top: 488px; width: 601px; height: 342px;
    background: linear-gradient(135deg, var(--brand-blue-light) 0%, var(--brand-blue) 40%, var(--brand-blue-deep) 100%); }
  .back-brand { position: absolute; left: 0; right: 0; top: 150px; text-align: center; color: #fff; font-weight: 700; line-height: 1; }
  .back-brand .line-main { display: block; font-size: 52px; letter-spacing: 1px; }
  .back-brand .line-sub { display: block; font-size: 20px; letter-spacing: 4px; margin-top: 8px; }
</style>
</head>
<body>
<div class="canvas">

  <section class="card card-front">
    <div class="brand-name">
      <span class="line-main">BROOKVALE</span>
      <span class="line-sub">ESTATES LLC</span>
    </div>

    <div class="name-accent"></div>
    <div class="person-name">DANIEL HARLOW</div>
    <div class="person-title">Property Manager</div>
    <div class="title-rule"></div>

    <ul class="contact-list">
      <li>
        <svg viewBox="0 0 24 24" aria-hidden="true"><path d="M6.6 10.8c1.4 2.8 3.8 5.1 6.6 6.6l2.2-2.2c.3-.3.7-.4 1-.2 1.1.4 2.3.6 3.6.6.6 0 1 .4 1 1V20c0 .6-.4 1-1 1C10.6 21 3 13.4 3 4c0-.6.4-1 1-1h3.5c.6 0 1 .4 1 1 0 1.3.2 2.5.6 3.6.1.3 0 .7-.2 1L6.6 10.8z"/></svg>
        555-214-7730
      </li>
      <li>
        <svg viewBox="0 0 24 20" aria-hidden="true"><rect x="6" y="0" width="12" height="6"/><rect x="1" y="7" width="22" height="8" rx="1"/><rect x="6" y="13" width="12" height="7"/></svg>
        555-214-7731
      </li>
      <li>
        <svg viewBox="0 0 24 18" aria-hidden="true"><path d="M1 1h22v16H1z M3 3v1l9 6 9-6V3z" fill-rule="evenodd"/></svg>
        daniel@brookvaleestates.us
      </li>
    </ul>

    <div class="address-block">
      1820 Alder Ridge Road #B210<br>
      Fairview, CA 90210<br>
      www.brookvaleestates.us
    </div>

    <div class="band-blue"></div>
    <div class="band-mark"></div>
    <div class="slogan-band">Multifamily Property Management</div>
  </section>

  <section class="card card-back">
    <div class="back-brand">
      <span class="line-main">BROOKVALE</span>
      <span class="line-sub">ESTATES LLC</span>
    </div>
  </section>

</div>
</body>
</html>
```